Awesome new dental practice requires a New Letterhead design

We would like a new letterhead design to align with our new business branding & business cards. I have uploaded all the logos & current business card details that can be used. The new website can be viewed here https://velortis.com.au

Other useful details: Font Poppins
Colour Palettes:
Dark Pink #c45389
Light Pink: #e83e8c
Black

Please let me know if you have any questions or require anything else.

Dental

• Poppins

```html
<!DOCTYPE html>
<html lang="en">
<head>
<meta charset="utf-8">
<title>Velortis Letterhead</title>
<link rel="stylesheet" href="https://fonts.googleapis.com/css2?family=Poppins:wght@400;500;600&family=Open+Sans:wght@400;600&display=swap">
<style>
  :root {
    --backdrop: #b2b2b2;
    --paper: #fafafa;
    --ink: #111111;
    --body-text: #5e5e5e;
    --pink-dark: #c45389;
    --pink-light: #e83e8c;
    --band: #d04685;
    --signature-tone: #d6e8f5;
  }
  * { margin: 0; padding: 0; box-sizing: border-box; }
  html, body { width: 1200px; height: 1001px; overflow: hidden; }
  body { background: var(--backdrop); position: relative; font-family: "Open Sans", sans-serif; }

  .letterhead {
    position: absolute; left: 287px; top: 58px;
    width: 625px; height: 885px;
    background: var(--paper); overflow: hidden;
  }

  .brand { position: absolute; top: 64px; left: 0; width: 100%; text-align: center; font-family: "Poppins", sans-serif; }
  .brand-name { font-size: 32px; font-weight: 600; color: var(--pink-dark); line-height: 1; letter-spacing: 0.5px; }
  .brand-name::after { content: ""; display: inline-block; width: 10px; height: 10px; background: var(--ink); margin-left: 8px; vertical-align: 4px; }
  .brand-sub { font-size: 9.5px; font-weight: 600; color: var(--ink); letter-spacing: 1.8px; margin-top: 6px; }

  .letter-body { position: absolute; left: 59px; width: 507px; color: var(--body-text); font-size: 9px; }
  .salutation { top: 211px; }
  .paragraphs { top: 259px; }
  .paragraphs p { line-height: 16px; text-align: justify; margin-bottom: 15px; }

  .sign-off { position: absolute; left: 59px; top: 594px; font-size: 9px; color: var(--body-text); }
  .sign-off .name-label { font-weight: 600; color: #444; }
  .signature { display: block; margin: 8px 0 8px; width: 152px; height: 32px; background: var(--signature-tone); border-radius: 4px; }

  .contact { position: absolute; left: 0; width: 100%; top: 794px; text-align: center; font-family: "Poppins", sans-serif; font-size: 9.5px; color: var(--ink); }
  .contact-row { display: flex; justify-content: center; align-items: center; gap: 12px; }
  .contact-item { display: inline-flex; align-items: center; gap: 6px; }
  .contact-item svg { width: 9px; height: 9px; fill: var(--pink-light); }
  .address { margin-top: 6px; }

  .footer-band { position: absolute; left: 0; bottom: 0; width: 625px; height: 45px; }
  .tagline { position: absolute; left: 0; bottom: 12px; width: 100%; text-align: center; font-family: "Poppins", sans-serif; font-weight: 500; font-size: 11.5px; color: #fff; }
</style>
</head>
<body>
  <main class="letterhead">
    <header class="brand">
      <div class="brand-name">Velortis</div>
      <div class="brand-sub">DENTISTRY &amp; ORTHODONTICS</div>
    </header>

    <p class="letter-body salutation">Dear Sir,</p>

    <section class="letter-body paragraphs">
      <p>Lorem Ipsum is simply dummy text of the printing and typesetting industry. Lorem Ipsum has been the industry's standard dummy text ever since the 1500s, when an unknown printer took a galley of type and scrambled it to make a type specimen book. It has survived not only five centuries, but also the leap into electronic typesetting, remaining essentially unchanged. It was popularised in the 1960s with the release of Letraset sheets containing Lorem Ipsum passages, and more recently with desktop publishing software like Aldus PageMaker including versions of Lorem Ipsum.</p>
      <p>Lorem Ipsum is simply dummy text of the printing and typesetting industry. Lorem Ipsum has been the industry's standard dummy text ever since the 1500s, when an unknown printer took a galley of type and scrambled it to make a type specimen book. It has survived not only five centuries, but also the leap into electronic typesetting, remaining essentially unchanged. It was popularised in the 1960s with the release of Letraset sheets containing Lorem Ipsum passages, and more recently with desktop publishing software like Aldus PageMaker including versions of Lorem Ipsum.</p>
      <p>Lorem Ipsum is simply dummy text of the printing and typesetting industry. Lorem Ipsum has been the industry's standard dummy text ever since the 1500s, when an unknown printer took a galley of type and scrambled it to make a type specimen book.</p>
    </section>

    <section class="sign-off">
      <p class="name-label">Your Name</p>
      <span class="signature" role="img" aria-label="Handwritten signature of Marcus Feldan"></span>
      <p>CEO &nbsp;|&nbsp; Owner</p>
    </section>

    <footer>
      <div class="contact">
        <div class="contact-row">
          <span class="contact-item"><svg viewBox="0 0 10 10"><path d="M1 3.5C1 2 2.5 1 5 1s4 1 4 2.5L7.5 4.5 6.5 3h-3l-1 1.5z M2.5 5h5l1 4h-7z"/></svg>(08) 9000 4821</span>
          <span class="contact-item"><svg viewBox="0 0 10 10"><path d="M0 2h10v6H0z M0 2l5 3.5L10 2" stroke="#fff" stroke-width="0.8"/></svg>hello@velortis.com.au</span>
          <span class="contact-item"><svg viewBox="0 0 10 10"><circle cx="5" cy="5" r="4.5"/><path d="M0.5 5h9M5 0.5v9" stroke="#fff" stroke-width="0.7"/></svg>www.velortis.com.au</span>
        </div>
        <div class="address">Shop 7, 82 Marlow Street Port Kessel WA 6790</div>
      </div>

      <svg class="footer-band" viewBox="0 0 625 45" preserveAspectRatio="none" aria-hidden="true">
        <path d="M0 18 Q312 -18 625 18 V45 H0 Z" fill="var(--ink)"/>
        <path d="M0 22 Q312 -12 625 22 V45 H0 Z" fill="var(--band)"/>
      </svg>
      <p class="tagline">Life is short. Smile while you still have teeth.</p>
    </footer>
  </main>
</body>
</html>
```